Business card design Needed for new logo / Construction business, home extensions and new builds

We need a business card design using our new logo files which i will attach to this project :)

We are a small construction business specialising in home extensions, new builds and property development. We are very ambitious and would appreciate professional and elegant designs for our new business card.

Very serious about using the services on MakerQuarry and recently acquired our new logo from here :)

Please get involved, i will feedback when i can as i am very busy but can respond daily, thanks

Target Market(s)

People that want to build onto their houses, new building developments or adding too their existing property

Industry/Entity Type

Construction

Contact Information for Business Card

Renwick Tolliver Construction, Lionel Ashby (Managing Director), Tel 07822254961, email - info@renwick-tolliver, www.renwick-tolliver.co.uk

Colors

Designer to choose colors to be used in the design.

Requirements
Must have
• I like a deep grey on the back please. A lot of you have provided black from and back, try mixing things up a little. The black looks cool 😎 Thanks

```html
<!DOCTYPE html>
<html lang="en">
<head>
<meta charset="utf-8">
<title>Renwick Tolliver Construction – Business Card</title>
<link href="https://fonts.googleapis.com/css2?family=Cinzel:wght@500&family=Lato:wght@400;700&display=swap" rel="stylesheet">
<style>
  :root {
    --backdrop: #141414;
    --card-front: #1b1b1b;
    --card-back: #333335;
    --gold: #d9a536;
    --gold-light: #f3d088;
    --silver: #d4d6d9;
    --text-light: #e8e8e8;
  }
  * { box-sizing: border-box; margin: 0; padding: 0; }
  html, body { width: 1200px; height: 801px; overflow: hidden; }
  body {
    background: var(--backdrop);
    font-family: "Lato", Arial, sans-serif;
    position: relative;
  }
  .card {
    position: absolute;
    top: 246px;
    width: 540px;
    height: 309px;
    box-shadow: 0 12px 30px rgba(0,0,0,0.55);
    overflow: hidden;
  }
  .card--front { left: 40px; background: var(--card-front); }
  .card--back { left: 620px; background: var(--card-back); }

  /* large square accent, cropped across the seam between the two sides */
  .accent-square {
    position: absolute;
    top: 44px;
    width: 230px;
    height: 230px;
    background: linear-gradient(135deg, var(--gold) 0%, var(--gold-light) 50%, var(--gold) 100%);
  }
  .card--front .accent-square { right: -125px; }
  .card--back .accent-square { left: -105px; }

  .contact { position: absolute; left: 40px; top: 58px; }
  .contact__name {
    font-family: "Cinzel", Georgia, serif;
    font-weight: 500;
    font-size: 24px;
    letter-spacing: 1px;
    color: var(--gold);
  }
  .contact__title { font-size: 14px; color: var(--silver); margin-top: 2px; }
  .contact__company { font-size: 13px; font-weight: 700; color: var(--text-light); margin-top: 16px; }
  .contact__address { font-size: 13px; color: var(--text-light); line-height: 1.4; }
  .contact__list { list-style: none; margin-top: 14px; }
  .contact__item {
    display: flex; align-items: center; gap: 10px;
    font-size: 13px; color: var(--text-light); line-height: 1.65;
  }
  .contact__icon { width: 12px; height: 12px; fill: var(--gold); flex: none; }

  .brand {
    position: absolute;
    left: 160px;
    right: 20px;
    top: 0;
    bottom: 0;
    display: flex;
    align-items: center;
    justify-content: center;
    text-align: center;
    font-family: "Cinzel", Georgia, serif;
    font-weight: 500;
    font-size: 24px;
    line-height: 1.3;
    letter-spacing: 1.5px;
    color: var(--gold);
  }
</style>
</head>
<body>
  <section class="card card--front">
    <div class="contact">
      <h1 class="contact__name">Lionel Ashby</h1>
      <p class="contact__title">Managing Director</p>
      <p class="contact__company">Renwick Tolliver Construction</p>
      <p class="contact__address">Your Address, City<br>State, Zip 1235</p>
      <ul class="contact__list">
        <li class="contact__item">
          <svg class="contact__icon" viewBox="0 0 24 24" aria-hidden="true"><path d="M6.6 10.8a15.1 15.1 0 0 0 6.6 6.6l2.2-2.2c.3-.3.7-.4 1-.2 1.1.4 2.3.6 3.6.6.6 0 1 .4 1 1V20c0 .6-.4 1-1 1A17 17 0 0 1 3 4c0-.6.4-1 1-1h3.5c.6 0 1 .4 1 1 0 1.3.2 2.5.6 3.6.1.3 0 .7-.2 1z"/></svg>
          07822254961
        </li>
        <li class="contact__item">
          <svg class="contact__icon" viewBox="0 0 24 24" aria-hidden="true"><path d="M2 5h20v14H2z M2 5l10 8 10-8" stroke="#1b1b1b" stroke-width="1.5"/></svg>
          info@renwick-tolliver.co.uk
        </li>
        <li class="contact__item">
          <svg class="contact__icon" viewBox="0 0 24 24" aria-hidden="true"><circle cx="12" cy="12" r="10"/></svg>
          renwick-tolliver.co.uk
        </li>
      </ul>
    </div>
    <div class="accent-square"></div>
  </section>

  <section class="card card--back">
    <div class="accent-square"></div>
    <div class="brand">Renwick Tolliver<br>Construction</div>
  </section>
</body>
</html>
```